Business card for a new innovative and professional lawn care business

We need a business card design for a new lawn care business in Halifax NS Canada. We offer lawn services in Halifax & Bedford. Our services offered include lawn care, garden services, and property maintenance. We take pride in our work and are experienced at what we do. I would like to see a design that is double sided. On the backside I would like the something simple (maybe my logo preferably on blackround (linked below) with website link, Facebook page or something). The front I want to include contact info:
Morgan Pell
phone 902-555-0148
email - brookvaleyards.ca
facebook - Facebook.com/brookvaleyards
Instagram maybe ? - instagram.com/brookvaleyard
Serving Halifax and Bedford for 5 years?
I don't want it to have too much information as I will be passing them out in aim to visit website, or call !
We do want it to include lawn care, garden services and property maintenance.
Basic, catchy, and modern looking !
Logo attached below !

Target Market(s)

Passing business cards to everyone I meet or interact with.

Industry/Entity Type

Lawn Care

Contact Information for Business Card

Double sided with some basic information, with catchy colours and easy to look at.

Font styles to use
Sans Serif

Requirements
Must have
• Must be double sided and have :
• Name, Phone, Email, FB, Website, and 3 main services offered - lawn care, property maintenance, garden services
Nice to have
• Would be nice to have instagram link if it goes well on there
Should not have
• Don't want too much writing or images that are distracting

```html
<!DOCTYPE html>
<html lang="en">
<head>
<meta charset="utf-8">
<title>Brookvale Yards – Business Card</title>
<link href="https://fonts.googleapis.com/css2?family=Montserrat:wght@400;600;700;800&display=swap" rel="stylesheet">
<style>
  :root {
    --backdrop: #1e1e1e;
    --card-dark: #353535;
    --card-light: #f7f7f7;
    --stripe: #ececec;
    --green: #8cc63f;
    --green-deep: #3c9a3c;
    --ink: #222222;
    --ink-soft: #4a4a4a;
  }
  * { box-sizing: border-box; margin: 0; padding: 0; }
  html, body {
    width: 1200px; height: 873px; overflow: hidden;
    background: var(--backdrop);
    font-family: "Montserrat", sans-serif;
  }
  .canvas { position: relative; width: 1200px; height: 873px; }

  /* Back side */
  .card-back {
    position: absolute; left: 70px; top: 276px;
    width: 576px; height: 330px;
    background: var(--card-dark);
    box-shadow: 0 10px 30px rgba(0,0,0,.5);
    overflow: hidden;
  }
  .card-back .brand {
    position: absolute; left: 0; right: 0; top: 108px;
    text-align: center;
  }
  .brand-name {
    display: inline-flex; align-items: center; gap: 12px;
    font-weight: 800; color: var(--green); letter-spacing: 1px;
    text-transform: uppercase;
  }
  .brand-name .mark {
    width: 18px; height: 18px; border-radius: 50%; background: var(--green);
  }
  .card-back .brand-name { font-size: 44px; }
  .card-back .brand-name .mark { width: 26px; height: 26px; }
  .service-band {
    position: absolute; left: 0; right: 0; bottom: 0; height: 62px;
    background: var(--green);
    display: flex; align-items: center; justify-content: center; gap: 30px;
    font-weight: 700; font-size: 16px; color: var(--ink);
  }
  .service-band li { list-style: none; display: flex; align-items: center; gap: 8px; }
  .service-band li::before {
    content: ""; width: 10px; height: 10px; border-radius: 50%; background: #f2f2f2;
  }

  /* Front side */
  .card-front {
    position: absolute; left: 730px; top: 150px;
    width: 330px; height: 576px;
    background: var(--card-light);
    box-shadow: 0 10px 30px rgba(0,0,0,.5);
    overflow: hidden;
  }
  .person { position: absolute; left: 34px; top: 40px; }
  .person-name { font-size: 22px; font-weight: 400; color: var(--green); }
  .person-name strong { font-weight: 700; }
  .person-role { font-size: 12px; color: var(--ink-soft); margin-top: 4px; }
  .card-front .brand {
    position: absolute; left: 0; right: 0; top: 158px; text-align: center;
  }
  .card-front .brand-name { font-size: 27px; }
  .contact-list {
    position: absolute; left: 0; right: 0; top: 298px; list-style: none;
  }
  .contact-list li {
    height: 52px; display: flex; align-items: center; gap: 16px;
    padding-left: 34px; font-size: 15px; color: var(--ink);
    border-top: 1px solid #e4e4e4;
  }
  .contact-list li:nth-child(odd) { background: var(--stripe); }
  .contact-list svg { width: 26px; height: 26px; flex: none; }
  .social-dot {
    width: 22px; height: 22px; margin: 0 2px; border-radius: 4px;
    background: var(--green-deep); flex: none;
  }
</style>
</head>
<body>
<div class="canvas">

  <section class="card-back" aria-label="Card back">
    <div class="brand">
      <span class="brand-name"><span class="mark"></span>Brookvale Yards</span>
    </div>
    <ul class="service-band">
      <li>Lawn Care</li>
      <li>Property Maintenance</li>
      <li>Garden Services</li>
    </ul>
  </section>

  <section class="card-front" aria-label="Card front">
    <div class="person">
      <p class="person-name">Morgan <strong>Pell</strong></p>
      <p class="person-role">Owner / Director</p>
    </div>
    <div class="brand">
      <span class="brand-name"><span class="mark"></span>Brookvale Yards</span>
    </div>
    <ul class="contact-list">
      <li>
        <svg viewBox="0 0 24 24" aria-hidden="true"><path fill="#3c9a3c" d="M6.6 10.8a15 15 0 0 0 6.6 6.6l2.2-2.2a1 1 0 0 1 1-.25 11.4 11.4 0 0 0 3.6.57 1 1 0 0 1 1 1V20a1 1 0 0 1-1 1A17 17 0 0 1 3 4a1 1 0 0 1 1-1h3.5a1 1 0 0 1 1 1c0 1.25.2 2.45.57 3.6a1 1 0 0 1-.25 1z"/></svg>
        902-555-0148
      </li>
      <li>
        <svg viewBox="0 0 24 24" aria-hidden="true"><rect x="2" y="5" width="20" height="14" rx="1" fill="#3c9a3c"/><path d="M3 6l9 7 9-7" fill="none" stroke="#f7f7f7" stroke-width="1.6"/></svg>
        me@brookvaleyards.ca
      </li>
      <li>
        <svg viewBox="0 0 24 24" aria-hidden="true"><circle cx="12" cy="12" r="10" fill="none" stroke="#3c9a3c" stroke-width="2"/><ellipse cx="12" cy="12" rx="4" ry="10" fill="none" stroke="#3c9a3c" stroke-width="1.6"/><path d="M2 12h20" stroke="#3c9a3c" stroke-width="1.6"/></svg>
        www.brookvaleyards.ca
      </li>
      <li><span class="social-dot"></span>/brookvaleyards</li>
      <li><span class="social-dot"></span>/brookvaleyard</li>
    </ul>
  </section>

</div>
</body>
</html>
```